New Business Card Design for Manufacturing

We are an engineering/manufacturing company that offers Advanced machining/assembly/engineering services, as well as innovative products for the heavy duty engine cooling markets.

We are looking to get a new business card designed that is clean and modern looking, but still fits the wide range of technical/skilled work we do.

- We hope to use this design as the base for other design work in new Presentations, web, and print work.

Industry/Entity Type

Engineering

Contact Information for Business Card

Our preferred color of blue is (RGB) 22/71/159 but can vary slightly from that color. Our content will be our Logo and full company name (Vantrell Forge Works, Inc.), company address, name, job title, phone number with extension, cell number, fax number, website, and email address on the cards.
We'd like the full company name next to the logo, but we are open to other interpretations of that layout.
Preferably, we would like the back side to be clean with just our logo, and the front to contain all of the contact information.

Colors
2f74b4
0355a3
85abd2

Requirements
Must have
• - Logo, company name, needed content - We are open to interpretation beyond that.
• - Standard size business card.
• - Horizontal orientation.
• - Enough space for lengthy names / job titles (for example, a job title could read "Directory of Human Resources" or "V.P. of Governmental Affairs"). We need this to look clean, whether the title be short (CEO) or long (as described above).

```html
<!DOCTYPE html>
<html lang="en">
<head>
<meta charset="utf-8">
<title>Vantrell Forge Works – Business Card</title>
<link href="https://fonts.googleapis.com/css2?family=Montserrat:wght@400;500;700;800&display=swap" rel="stylesheet">
<style>
  :root {
    --brand-blue: #16479f;
    --deep-blue: #0355a3;
    --soft-blue: #85abd2;
    --ink-blue: #1f4fa6;
    --paper: #ffffff;
    --stage: #3a3a3c;
  }
  * { margin: 0; padding: 0; box-sizing: border-box; }
  html, body { width: 1200px; height: 880px; overflow: hidden; }
  body {
    background: var(--stage);
    font-family: "Montserrat", sans-serif;
    position: relative;
  }
  .card {
    position: absolute;
    left: 285px;
    width: 630px;
    height: 360px;
    border-radius: 26px;
    overflow: hidden;
    box-shadow: 0 14px 30px rgba(0,0,0,0.35);
  }
  /* Back side */
  .card-back {
    top: 60px;
    background: var(--brand-blue);
    color: var(--paper);
  }
  .card-back .wordmark {
    position: absolute;
    left: 0; right: 0;
    top: 140px;
    text-align: center;
    font-weight: 800;
    font-size: 34px;
    letter-spacing: 0.5px;
    text-transform: uppercase;
  }
  .card-back .website {
    position: absolute;
    left: 0; right: 0;
    top: 232px;
    text-align: center;
    font-size: 14px;
    letter-spacing: 5px;
  }
  /* Front side */
  .card-front {
    top: 460px;
    background: var(--paper);
  }
  .card-front .band { position: absolute; inset: 0; width: 630px; height: 360px; }
  .holder {
    position: absolute;
    right: 40px;
    top: 34px;
    text-align: right;
    color: var(--paper);
  }
  .holder-name { font-weight: 700; font-size: 19px; letter-spacing: 0.5px; }
  .holder-title { font-size: 13px; margin-top: 2px; }
  .company-name {
    position: absolute;
    left: 40px;
    top: 180px;
    color: var(--brand-blue);
    font-weight: 800;
    font-size: 26px;
    text-transform: uppercase;
    letter-spacing: 0.3px;
  }
  .rule {
    position: absolute;
    left: 36px; right: 36px;
    top: 238px;
    height: 1px;
    background: var(--soft-blue);
  }
  .contacts {
    position: absolute;
    left: 36px; right: 36px;
    top: 256px;
    display: flex;
    color: var(--ink-blue);
    font-size: 13px;
  }
  .contact-group {
    padding: 4px 18px;
    display: flex;
    flex-direction: column;
    gap: 8px;
  }
  .contact-group + .contact-group { border-left: 1px solid var(--soft-blue); }
  .contact-group:first-child { padding-left: 0; }
  .contact-line { display: flex; align-items: center; gap: 8px; white-space: nowrap; }
  .icon { width: 18px; height: 18px; flex: none; }
</style>
</head>
<body>

<section class="card card-back" aria-label="Card back">
  <div class="wordmark">Vantrell Forge Works, Inc.</div>
  <div class="website">www.vantrellforge.com</div>
</section>

<section class="card card-front" aria-label="Card front">
  <svg class="band" viewBox="0 0 630 360" aria-hidden="true">
    <path d="M0 0 H630 V150 Q330 60 0 140 Z" fill="var(--brand-blue)"/>
    <path d="M30 160 Q330 78 630 168" fill="none" stroke="var(--soft-blue)" stroke-width="9"/>
  </svg>

  <div class="holder">
    <div class="holder-name">DANA WHITLOCK</div>
    <div class="holder-title">Founder</div>
  </div>

  <div class="company-name">Vantrell Forge Works, Inc.</div>
  <div class="rule"></div>

  <div class="contacts">
    <div class="contact-group">
      <div class="contact-line">
        <svg class="icon" viewBox="0 0 18 18" aria-hidden="true"><circle cx="9" cy="9" r="8" fill="none" stroke="var(--soft-blue)"/><rect x="6" y="4.5" width="6" height="9" rx="1" fill="none" stroke="var(--ink-blue)"/></svg>
        (555) 014-2290
      </div>
      <div class="contact-line">
        <svg class="icon" viewBox="0 0 18 18" aria-hidden="true"><circle cx="9" cy="9" r="8" fill="none" stroke="var(--soft-blue)"/><path d="M5 10.5 q4-5 8 0 v1.5 h-8z" fill="var(--ink-blue)"/></svg>
        (555) 014-2291
      </div>
    </div>
    <div class="contact-group">
      <div class="contact-line">
        <svg class="icon" viewBox="0 0 18 18" aria-hidden="true"><circle cx="9" cy="9" r="8" fill="none" stroke="var(--soft-blue)"/><rect x="5" y="6" width="8" height="6" fill="none" stroke="var(--ink-blue)"/><path d="M5 6 L9 9.5 L13 6" fill="none" stroke="var(--ink-blue)"/></svg>
        info@vantrellforge.com
      </div>
      <div class="contact-line">
        <svg class="icon" viewBox="0 0 18 18" aria-hidden="true"><circle cx="9" cy="9" r="8" fill="none" stroke="var(--soft-blue)"/><circle cx="9" cy="9" r="4.5" fill="none" stroke="var(--ink-blue)"/><path d="M4.5 9 H13.5 M9 4.5 V13.5" stroke="var(--ink-blue)"/></svg>
        www.vantrellforge.com
      </div>
    </div>
    <div class="contact-group">
      <div class="contact-line">PO Box 418 Harlow Road</div>
      <div class="contact-line">2nd Street Brackenfield</div>
    </div>
  </div>
</section>

</body>
</html>
```